Design a Website for an IT Support Company

We are an IT support company that provides commercial IT support and services to small and medium sized businesses. We are in need of a website to be developed for our business.
We would like to work with someone who is either familiar with the IT field, or has developed a website for an IT support company in the past.
Some examples of designs/layouts that we like:
https://www.veldaworks.example/
http://www.marsbyquill.example/
http://817kq.example/
http://www.olbenstructures.example/
http://www.bykq.example/
I have attached a word document that gives a menu system/page layout format that we would like for our website as well as branch office phone numbers. Our logo is also attached that you can use for your design purposes. We currently do not have copy produced for all of the pages outlined in the word document, but would get this done during the project with the selected designer.
We would like the website to be SEO friendly & fully responsive. We would prefer a Wordpress format, however, we are open to HTML formats as well.

```html
<!DOCTYPE html>
<html lang="en">
<head>
<meta charset="utf-8">
<title>Corvane IT – IT Support for Small and Medium Businesses</title>
<link href="https://fonts.googleapis.com/css2?family=Open+Sans:wght@400;600;700;800&display=swap" rel="stylesheet">
<style>
:root{
  --blue:#0b6bbf;
  --blue-dark:#0a5ea8;
  --ink:#333;
  --muted:#555;
  --dark:#2c2c2c;
  --darker:#1f1f1f;
  --green:#3fa535;
  --card:#fff;
  --light:#f2f2f2;
  --line:#e2e2e2;
}
*{margin:0;padding:0;box-sizing:border-box}
html,body{width:1200px;height:3838px;overflow:hidden}
body{font-family:"Open Sans",Arial,sans-serif;color:var(--ink);background:#fff;position:relative}
.abs{position:absolute}
/* header */
.site-header{position:absolute;top:0;left:0;width:1200px;height:120px;background:#fff}
.brand{position:absolute;left:75px;top:22px;display:flex;align-items:center;gap:14px}
.brand-mark{width:46px;height:46px;border-radius:50%;background:var(--blue)}
.brand-name{font-size:34px;font-weight:700;color:var(--blue);letter-spacing:-.5px}
.cta-top{position:absolute;left:512px;top:18px;width:390px;height:38px;border:2px solid var(--green);color:var(--green);font-size:13px;font-weight:700;display:flex;align-items:center;justify-content:center}
.phone-top{position:absolute;left:928px;top:18px;display:flex;align-items:center;gap:12px;color:var(--blue);font-size:25px;font-weight:700}
.phone-dot{width:36px;height:36px;border-radius:50%;background:#666;display:flex;align-items:center;justify-content:center}
.main-nav{position:absolute;right:72px;top:82px;display:flex;gap:46px;font-size:14px;font-weight:700;color:#333}
.main-nav .active{color:var(--blue);border-bottom:3px solid var(--blue);padding-bottom:6px}
/* hero */
.hero{position:absolute;top:120px;left:0;width:1200px;height:555px;background:linear-gradient(100deg,#c9c9c4 0%,#e3e3df 45%,#8d8f92 70%,#d7d7d3 100%)}
.hero-caption{position:absolute;left:75px;top:195px;width:545px;background:rgba(0,0,0,.82);padding:16px 22px 18px}
.hero-caption h1{font-size:39px;font-weight:800;color:#fff;line-height:1}
.hero-caption h1 span{color:#2f9ae6}
.hero-caption p{color:#fff;font-size:19px;font-weight:700;line-height:1.4;margin-top:10px}
.hero-dots{position:absolute;left:575px;top:520px;display:flex;gap:7px}
.hero-dots i{width:12px;height:12px;border-radius:50%;background:#fff;display:block}
.hero-dots i.on{background:var(--blue)}
/* services */
.section-title{position:absolute;left:0;width:1200px;text-align:center;font-size:25px;font-weight:700;color:#333;letter-spacing:.5px}
.service{position:absolute;top:775px;width:332px;height:330px;background:var(--card);box-shadow:0 2px 10px rgba(0,0,0,.18);padding:32px 26px}
.service-head{display:flex;align-items:center;gap:26px;margin-bottom:20px}
.service-head h3{font-size:24px;font-weight:700;color:var(--blue)}
.service ul{list-style:none}
.service li{font-size:14.5px;color:#444;line-height:28.5px;display:flex;align-items:center;gap:14px}
.tick{flex:none}
.btn{display:inline-block;background:var(--blue);color:#fff;font-weight:700;font-size:12.5px;padding:11px 16px}
.service .btn{margin-top:16px}
/* welcome */
.welcome-photo{position:absolute;top:1166px;left:0;width:612px;height:577px;background:linear-gradient(120deg,#8fa0b3 0%,#d9dde2 40%,#b3b9c0 70%,#6d7680 100%)}
.welcome{position:absolute;top:1166px;left:612px;width:588px;height:577px;background:var(--dark);padding:64px 56px 0 29px;color:#e8e8e8}
.welcome h2{font-size:23px;font-weight:700;color:#fff;margin-bottom:14px}
.welcome p{font-size:14px;line-height:25.5px;margin-bottom:18px}
.welcome .btn{margin-top:12px;padding:14px 30px}
/* why */
.why{position:absolute;top:1743px;left:0;width:1200px;height:764px;background:var(--blue);color:#fff}
.why h2{text-align:center;font-size:25px;font-weight:700;margin-top:52px}
.why-list{position:absolute;left:75px;top:115px;width:615px;list-style:none}
.why-list li{display:flex;gap:14px;font-size:13.5px;line-height:22px;margin-bottom:18px}
.why-list b{font-weight:700;font-size:15px}
.tablet{position:absolute;left:740px;top:120px;width:388px;height:282px;background:#fafafa;border-radius:26px;box-shadow:0 4px 14px rgba(0,0,0,.3)}
.tablet-screen{position:absolute;left:38px;top:18px;width:312px;height:246px;background:linear-gradient(120deg,#c8ced6,#eef0f2 55%,#aeb6c0)}
.play{position:absolute;left:136px;top:103px;width:40px;height:40px;border-radius:50%;background:rgba(255,255,255,.85);display:flex;align-items:center;justify-content:center}
.watch{position:absolute;left:828px;top:545px;font-size:26px;font-weight:600;font-style:italic}
/* testimonials */
.quote{position:absolute;top:2612px;width:332px;height:212px;background:var(--light);padding:20px 26px;text-align:center}
.quote p{font-size:13px;font-style:italic;color:#555;line-height:21px}
.quote .who{margin-top:10px;font-size:13px;font-weight:700;color:var(--blue)}
.quote .mark{position:absolute;font-size:80px;color:#ddd;font-weight:800;line-height:1}
.avatar{position:absolute;top:2782px;width:74px;height:74px;border-radius:50%;background:linear-gradient(#b9bec4,#7b8189);border:3px solid #fff}
.t-dots{position:absolute;top:2896px;left:573px;display:flex;gap:7px}
.t-dots i{display:block;width:13px;height:13px;border-radius:50%;background:#555}
.t-dots i.on{background:var(--blue)}
/* partners */
.partners{position:absolute;top:2962px;left:0;width:1200px;height:190px;background:var(--light)}
.partner{position:absolute;top:97px;height:56px;background:#b8bcc2}
/* schedule */
.schedule{position:absolute;top:3152px;left:0;width:1200px;height:340px;background:var(--dark)}
.schedule h2{text-align:center;color:#fff;font-size:25px;font-weight:700;margin-top:52px}
.field{position:absolute;width:333px;height:42px;background:#fff;font-size:13px;color:#333;padding:12px 14px}
.schedule .submit{position:absolute;left:496px;top:242px;width:208px;height:48px;background:var(--green);color:#fff;font-size:14px;font-weight:700;display:flex;align-items:center;justify-content:center}
/* footer */
.site-footer{position:absolute;top:3492px;left:0;width:1200px;height:281px;background:var(--blue);color:#fff}
.footer-brand{position:absolute;left:75px;top:48px;display:flex;align-items:center;gap:10px;font-size:23px;font-weight:700}
.footer-brand i{display:block;width:30px;height:30px;border-radius:50%;background:#fff}
.contacts{position:absolute;left:75px;top:118px;font-size:12.5px;line-height:21.5px}
.contacts td:first-child{padding-right:26px}
.col-title{position:absolute;top:52px;font-size:13px;font-weight:700}
.sitemap{position:absolute;left:368px;top:82px;list-style:none;font-size:12.5px;line-height:31px}
.post{position:absolute;left:535px;display:flex;gap:14px;font-size:12px;line-height:16px;width:310px}
.post .thumb{flex:none;width:68px;height:52px;background:linear-gradient(#d8dde3,#98a2ad)}
.post b{display:block;font-size:13px}
.email{position:absolute;left:883px;top:84px;width:242px;height:40px;background:#fff;color:#666;font-size:12px;padding:12px}
.signup{position:absolute;left:1035px;top:136px;width:90px;height:40px;background:#1a1a1a;font-size:13px;font-weight:700;display:flex;align-items:center;justify-content:center}
.bottom-bar{position:absolute;top:3773px;left:0;width:1200px;height:65px;background:var(--darker);color:#888;font-size:11.5px}
.bottom-bar p{position:absolute;left:75px;top:25px}
.socials{position:absolute;right:75px;top:22px;display:flex;gap:18px}
.socials i{display:block;width:20px;height:20px;border-radius:50%;background:#fff}
</style>
</head>
<body>

<header class="site-header">
  <div class="brand"><span class="brand-mark"></span><span class="brand-name">Corvane IT</span></div>
  <div class="cta-top">SCHEDULE A FREE NETWORK ASSESSMENT TODAY!</div>
  <div class="phone-top">
    <span class="phone-dot"><svg width="18" height="18" viewBox="0 0 24 24"><path fill="#fff" d="M6.6 10.8a15 15 0 0 0 6.6 6.6l2.2-2.2c.3-.3.7-.4 1-.2 1.1.4 2.3.6 3.6.6.6 0 1 .4 1 1V20c0 .6-.4 1-1 1A17 17 0 0 1 3 4c0-.6.4-1 1-1h3.5c.6 0 1 .4 1 1 0 1.3.2 2.5.6 3.6.1.3 0 .7-.2 1z"/></svg></span>
    555-014-2200
  </div>
  <nav class="main-nav"><span class="active">HOME</span><span>DATA</span><span>CLOUD</span><span>VOICE</span><span>CONTACT</span></nav>
</header>

<section class="hero" role="img" aria-label="Photo of a desk phone on an office desk">
  <div class="hero-caption">
    <h1>BUSINESS <span>PHONE SYSTEMS</span></h1>
    <p>We are an IT support company that provides commercial IT support and services to small and medium sized businesse.</p>
  </div>
  <div class="hero-dots"><i></i><i></i><i class="on"></i></div>
</section>

<h2 class="section-title" style="top:720px">OUR SERVICES</h2>

<svg width="0" height="0" style="position:absolute"><defs>
  <symbol id="tick" viewBox="0 0 14 14"><path d="M2 7.5l3.2 3L12 3.5" fill="none" stroke="#0b6bbf" stroke-width="2.4"/></symbol>
  <symbol id="tick-w" viewBox="0 0 16 16"><circle cx="8" cy="8" r="7.5" fill="#fff"/><path d="M4 8.3l2.6 2.5L12 5.3" fill="none" stroke="#0b6bbf" stroke-width="2.2"/></symbol>
</defs></svg>

<article class="service" style="left:75px">
  <div class="service-head">
    <svg width="48" height="54" viewBox="0 0 48 54"><ellipse cx="24" cy="8" rx="22" ry="7" fill="#222"/><path d="M2 13c0 4 10 7 22 7s22-3 22-7v10c0 4-10 7-22 7S2 27 2 23z" fill="#222"/><path d="M2 28c0 4 10 7 22 7s22-3 22-7v10c0 4-10 7-22 7S2 42 2 38z" fill="#222"/></svg>
    <h3>DATA</h3>
  </div>
  <ul>
    <li><svg class="tick" width="14" height="14"><use href="#tick"/></svg>Managed IT Services</li>
    <li><svg class="tick" width="14" height="14"><use href="#tick"/></svg>IT Support &amp; Consulting</li>
    <li><svg class="tick" width="14" height="14"><use href="#tick"/></svg>IT Helpdesk Services</li>
    <li><svg class="tick" width="14" height="14"><use href="#tick"/></svg>Network Security</li>
    <li><svg class="tick" width="14" height="14"><use href="#tick"/></svg>Data Backup &amp; Recovery</li>
  </ul>
  <span class="btn">READ MORE</span>
</article>

<article class="service" style="left:434px">
  <div class="service-head">
    <svg width="64" height="44" viewBox="0 0 64 44"><path d="M14 42a12 12 0 0 1-1-24 18 18 0 0 1 34-5 14 14 0 0 1 4 29z" fill="#222"/></svg>
    <h3>CLOUD</h3>
  </div>
  <ul>
    <li><svg class="tick" width="14" height="14"><use href="#tick"/></svg>Suite 365 Migrations</li>
    <li><svg class="tick" width="14" height="14"><use href="#tick"/></svg>Nimbus Web Services Management</li>
    <li><svg class="tick" width="14" height="14"><use href="#tick"/></svg>Cloud Migration Services</li>
    <li><svg class="tick" width="14" height="14"><use href="#tick"/></svg>Hosted Virtual Servers</li>
    <li><svg class="tick" width="14" height="14"><use href="#tick"/></svg>Hosted Telephone Systems</li>
  </ul>
  <span class="btn">READ MORE</span>
</article>

<article class="service" style="left:794px">
  <div class="service-head">
    <svg width="44" height="48" viewBox="0 0 24 24"><path fill="#222" d="M6.6 10.8a15 15 0 0 0 6.6 6.6l2.2-2.2c.3-.3.7-.4 1-.2 1.1.4 2.3.6 3.6.6.6 0 1 .4 1 1V20c0 .6-.4 1-1 1A17 17 0 0 1 3 4c0-.6.4-1 1-1h3.5c.6 0 1 .4 1 1 0 1.3.2 2.5.6 3.6.1.3 0 .7-.2 1z"/></svg>
    <h3>VOICE</h3>
  </div>
  <ul>
    <li><svg class="tick" width="14" height="14"><use href="#tick"/></svg>Starline Consulting</li>
    <li><svg class="tick" width="14" height="14"><use href="#tick"/></svg>Business Telephone Systems</li>
    <li><svg class="tick" width="14" height="14"><use href="#tick"/></svg>Multiple Office Phone Systems</li>
    <li><svg class="tick" width="14" height="14"><use href="#tick"/></svg>Granite VoIP Telephone Systems</li>
    <li><svg class="tick" width="14" height="14"><use href="#tick"/></svg>SIP Trunks</li>
  </ul>
  <span class="btn">READ MORE</span>
</article>

<div class="welcome-photo" role="img" aria-label="Photo of support staff with headsets working at computers"></div>
<section class="welcome">
  <h2>WELCOME TO OUR WEBSITE</h2>
  <p>Technology is the backbone of your business. Corvane IT excels at providing outsourced network IT support to businesses just like yours. Our team of friendly and highly experienced engineers are standing by to help you get the most out of your technology. Whether you are looking to augment your current in house IT staff, or outsource your IT needs entirely to a third-party vendor, we are your trusted resource for your IT consulting and network IT support needs.</p>
  <p>Corvane IT offers solutions in IT managed services, IT helpdesk services, network support, network security, servers and virtualization, disaster prevention and recovery solutions, cloud migration support, Suite 365 migration support, project management, business telephone systems, unified communications, Starline consulting, and much more.</p>
  <span class="btn">READ MORE</span>
</section>

<section class="why">
  <h2>WHY CORVANE IT</h2>
  <ul class="why-list">
    <li><svg width="16" height="16" style="flex:none;margin-top:3px"><use href="#tick-w"/></svg><div><b>Control IT Spending</b> - We offer an all-inclusive proactive, reliable, and affordable solution for your IT support needs. Many companies bill at an hourly rate, or by pre-paid blocks of time plus materials.</div></li>
    <li><svg width="16" height="16" style="flex:none;margin-top:3px"><use href="#tick-w"/></svg><div><b>Optimized IT Efficiency</b> - Technology is not a one size fits all approach. Corvane IT determines and implements solutions for your business that increase productivity and provide overall added value to your business model.</div></li>
    <li><svg width="16" height="16" style="flex:none;margin-top:3px"><use href="#tick-w"/></svg><div><b>Real Proactive Network Management</b> - Our approach to IT support and network management is based upon a proven checklist driven process that ensures your information systems and network are available when you need them.</div></li>
    <li><svg width="16" height="16" style="flex:none;margin-top:3px"><use href="#tick-w"/></svg><div><b>World Class Customer Support</b> - Immediate response times. If you need us on site for IT support, we're there. If you need remote IT support from our team, we're only a phone call away. Your satisfaction is 100% guaranteed.</div></li>
    <li><svg width="16" height="16" style="flex:none;margin-top:3px"><use href="#tick-w"/></svg><div><b>No Technical Jargon</b> - We provide clear and simple to understand answers to your computer and IT support questions. You'll never be made to feel stupid by any "technical talk" from our IT support specialists.</div></li>
    <li><svg width="16" height="16" style="flex:none;margin-top:3px"><use href="#tick-w"/></svg><div><b>Analytics and Reports</b> - We are constantly reviewing your existing environment to determine areas for operational improvement. Reports are sent out on a monthly basis that highlight various statistics.</div></li>
    <li><svg width="16" height="16" style="flex:none;margin-top:3px"><use href="#tick-w"/></svg><div><b>No Contracts</b> - We don't believe in locking you down into an agreement if we aren't delivering on the service level that you are paying for.</div></li>
  </ul>
  <div class="tablet">
    <div class="tablet-screen" role="img" aria-label="Video still of a support agent wearing a headset">
      <span class="play"><svg width="16" height="18" viewBox="0 0 16 18"><path d="M2 1l13 8-13 8z" fill="#0b6bbf"/></svg></span>
    </div>
  </div>
  <svg class="abs" style="left:858px;top:455px" width="150" height="90" viewBox="0 0 150 90"><path d="M8 84C60 74 110 50 138 10" fill="none" stroke="#fff" stroke-width="3"/><path d="M124 12l15-5-2 16" fill="none" stroke="#fff" stroke-width="3"/></svg>
  <div class="watch">Watch a Video</div>
</section>

<h2 class="section-title" style="top:2552px">CUSTOMER TESTIMONIALS</h2>
<div class="quote" style="left:75px"><span class="mark" style="left:4px;top:6px">“</span><span class="mark" style="right:8px;top:120px">”</span><p>Aliquam molestie, mi et imperdiet euismod, dui purus auctor tellus, et interdum lacus lectus et ante. Sed accumsan sollicitudin sapien, sit amet adipiscing turpis...</p><div class="who">-NAME HEADING</div></div>
<div class="quote" style="left:434px"><span class="mark" style="left:4px;top:6px">“</span><span class="mark" style="right:8px;top:120px">”</span><p>Aliquam molestie, mi et imperdiet euismod, dui purus auctor tellus, et interdum lacus lectus et ante. Sed accumsan sollicitudin sapien, sit amet adipiscing turpis...</p><div class="who">-NAME HEADING</div></div>
<div class="quote" style="left:794px"><span class="mark" style="left:4px;top:6px">“</span><span class="mark" style="right:8px;top:120px">”</span><p>Aliquam molestie, mi et imperdiet euismod, dui purus auctor tellus, et interdum lacus lectus et ante. Sed accumsan sollicitudin sapien, sit amet adipiscing turpis...</p><div class="who">-NAME HEADING</div></div>
<div class="avatar" style="left:204px" role="img" aria-label="Customer portrait"></div>
<div class="avatar" style="left:563px" role="img" aria-label="Customer portrait"></div>
<div class="avatar" style="left:923px" role="img" aria-label="Customer portrait"></div>
<div class="t-dots"><i class="on"></i><i></i><i></i></div>

<section class="partners">
  <h2 class="section-title" style="top:30px">OUR PARTNERS</h2>
  <div class="partner" style="left:78px;width:92px;border-radius:4px" role="img" aria-label="Partner badge"></div>
  <div class="partner" style="left:214px;width:136px" role="img" aria-label="Partner badge"></div>
  <div class="partner" style="left:392px;width:112px" role="img" aria-label="Partner badge"></div>
  <div class="partner" style="left:544px;width:222px" role="img" aria-label="Partner badge"></div>
  <div class="partner" style="left:800px;width:178px" role="img" aria-label="Partner badge"></div>
  <div class="partner" style="left:1040px;width:56px;border-radius:50%" role="img" aria-label="Partner badge"></div>
</section>

<section class="schedule">
  <h2>SCHEDULE A FREE NETWORK ASSESSMENT TODAY</h2>
  <div class="field" style="left:254px;top:126px">Name</div>
  <div class="field" style="left:613px;top:126px">Company Name</div>
  <div class="field" style="left:254px;top:168px;top:171px">Email Address</div>
  <div class="field" style="left:613px;top:171px">Phone No.</div>
  <div class="submit">SCHEDULE NOW</div>
</section>

<footer class="site-footer">
  <div class="footer-brand"><i></i>Corvane IT</div>
  <table class="contacts">
    <tr><td>Main Number:</td><td>555-014-2200</td></tr>
    <tr><td>Houston:</td><td>555-014-2310</td></tr>
    <tr><td>San Antonio:</td><td>555-014-2420</td></tr>
    <tr><td>Austin:</td><td>555-014-2530</td></tr>
    <tr><td>Tulsa:</td><td>555-014-2640</td></tr>
    <tr><td>Oklahoma City:</td><td>555-014-2750</td></tr>
  </table>
  <div class="col-title" style="left:368px">SITE MAP</div>
  <ul class="sitemap"><li>Home</li><li>Services</li><li>Why Corvane IT</li><li>Contact us</li></ul>
  <div class="col-title" style="left:535px">BLOG POSTS</div>
  <div class="post" style="top:90px"><span class="thumb" role="img" aria-label="Blog post thumbnail"></span><div><b>Consectetuer adipiscing elit</b>Aenean a nibh eget turpis vehicula tempus ac...</div></div>
  <div class="post" style="top:162px"><span class="thumb" role="img" aria-label="Blog post thumbnail"></span><div><b>Consectetuer adipiscing elit</b>Aenean a nibh eget turpis vehicula tempus ac...</div></div>
  <div class="col-title" style="left:883px">EMAIL SIGN UP</div>
  <div class="email">Enter Email Address</div>
  <div class="signup">SIGN UP</div>
</footer>

<div class="bottom-bar">
  <p>Copyright © 2017 Company Name. All Right Reserved</p>
  <div class="socials"><i></i><i></i><i></i><i></i><i></i></div>
</div>

</body>
</html>
```